Corporate Template

Looking for a set of corporate slides to be made which contain multiple different slides and orientations. Looking for at least 8 to 10 different master pages plus a Coversheet and closeout page. Incorporating a color palate similar to our logo coloring is preferred.
I have attached a logo.
I like the amber quill works designs best so far. They seem to fit what I'm looking for in terms of visual appearance.
Reason: I'm trying to allow time for a couple new designers to incorporate some changes I requested to their existing designs.

```html
<!DOCTYPE html>
<html lang="en">
<head>
<meta charset="utf-8">
<title>Corporate Template – Content Slides</title>
<link href="https://fonts.googleapis.com/css2?family=Arimo:ital,wght@0,400;0,700;1,400&display=swap" rel="stylesheet">
<style>
  :root {
    --stage-grey: #e6e6e6;
    --paper: #ffffff;
    --navy: #1b4a8c;
    --sky: #38a6e6;
    --body-grey: #7a7a7a;
    --rule: #7fd0f2;
    --corner-blue: #3ec1ee;
    --footer-blue: #1a8fe0;
    --footer-dark: #1d4f9a;
    --footer-light: #17c5f3;
    --footer-muted: #6cc2f5;
    --white: #ffffff;
  }
  * { box-sizing: border-box; margin: 0; padding: 0; }
  html, body { width: 1200px; height: 555px; overflow: hidden; }
  body {
    position: relative;
    background: var(--paper);
    font-family: "Arimo", Arial, sans-serif;
  }
  .stage {
    position: absolute; left: 0; top: 0;
    width: 1200px; height: 478px;
    background: var(--stage-grey);
  }
  .slide {
    position: absolute; top: 33px;
    width: 563px; height: 423px;
    background: var(--paper);
    overflow: hidden;
  }
  .slide--two-column { left: 27px; }
  .slide--single-column { left: 608px; }

  .slide__art { position: absolute; left: 0; top: 0; }

  .slide__title {
    position: absolute; left: 42px; top: 37px;
    font-size: 13px; font-weight: 700; color: var(--navy);
  }
  .slide__subtitle {
    position: absolute;
    font-size: 10.5px; color: var(--sky);
  }
  .subtitle--lead { left: 41px; top: 55px; }

  .copy {
    position: absolute;
    font-size: 8.1px; line-height: 10.3px; color: var(--body-grey);
  }

  .note {
    position: absolute;
    border-top: 1px solid var(--rule);
    border-bottom: 1px solid var(--rule);
    font-size: 8.1px; line-height: 10.3px; font-style: italic; color: var(--sky);
  }

  .bullet-list { position: absolute; list-style: none; }
  .bullet-list li {
    position: relative;
    font-size: 8.1px; line-height: 10.3px; color: var(--body-grey);
  }
  .bullet-list .globe-icon { position: absolute; left: 0; top: 0; }

  .footer-text {
    position: absolute; top: 390px;
    font-size: 10.5px; color: var(--white);
  }
  .footer-page { left: 42px; font-weight: 700; }
  .footer-title { left: 116px; color: var(--footer-muted); letter-spacing: 0.2px; }
  .footer-subtitle { left: 281px; font-weight: 700; }
  .footer-brand {
    position: absolute; left: 472px; top: 383px;
    font-size: 11px; line-height: 12px; font-weight: 700; color: var(--white);
    text-align: center; letter-spacing: 0.5px;
  }
</style>
</head>
<body>
  <div class="stage">

    <!-- Two-column content slide -->
    <section class="slide slide--two-column">
      <svg class="slide__art" width="563" height="423" viewBox="0 0 563 423" aria-hidden="true">
        <defs>
          <linearGradient id="cornerCyanA" x1="0" y1="0" x2="1" y2="1">
            <stop offset="0" stop-color="#7af3f7"/>
            <stop offset="1" stop-color="#3fd0f0"/>
          </linearGradient>
          <linearGradient id="footerDarkA" x1="0" y1="0" x2="1" y2="0">
            <stop offset="0" stop-color="#1d4f9a"/>
            <stop offset="1" stop-color="#1a8fe0"/>
          </linearGradient>
          <linearGradient id="footerLightA" x1="0" y1="0" x2="1" y2="0">
            <stop offset="0" stop-color="#13a6ec"/>
            <stop offset="1" stop-color="#17c5f3"/>
          </linearGradient>
        </defs>
        <polygon points="486,0 563,0 563,72" fill="var(--corner-blue)"/>
        <polygon points="0,267 0,371 100,371" fill="url(#cornerCyanA)"/>
        <rect x="0" y="371" width="563" height="52" fill="var(--footer-blue)"/>
        <polygon points="75,371 240,371 275,423 110,423" fill="url(#footerDarkA)"/>
        <polygon points="240,371 563,371 563,423 275,423" fill="url(#footerLightA)"/>
      </svg>

      <h1 class="slide__title">TITLE HERE</h1>
      <h2 class="slide__subtitle subtitle--lead">Subtitle here</h2>

      <p class="copy" style="left:42px; top:82px; width:212px;">Lorem ipsum dolor sit amet, consectetur adipiscing elit. Fusce et diam vitae mi viverra vulputate. Suspendisse tempus in tortor vitae egestas. Nam dapibus augue non sem placerat lacinia. Pellentesque augue odio, vulputate a purus vitae, semper mollis diam. Morbi consectetur pulvinar adipiscing. Sed et consectetur urna. Mauris id tempor magna, vel feugiat arcu. Nullam fermentum elementum aliquam. Duis vitae dictum tellus.</p>

      <p class="note" style="left:42px; top:188px; width:211px; padding:7px 5px 6px;">Important notes here. Lorem ipsum dolor sit amet, consectetur adipiscing elit.</p>

      <p class="copy" style="left:42px; top:237px; width:212px;">Maecenas mattis tempor nibh non laoreet. Curabitur malesuada, urna in posuere pulvinar, massa mauris feugiat turpis, a aliquam urna magna non diam. Sed eu tempor nibh. Aenean facilisis massa libero, vitae laoreet tortor mattis quis. Praesent egestas egestas leo, porta auctor libero volutpat quis. Fusce ac iaculis enim. Sed nec dapibus augue.</p>

      <p class="copy" style="left:311px; top:36px; width:215px;">Lorem ipsum dolor sit amet, consectetur adipiscing elit. Aliquam eget bibendum dui. Nunc tristique, orci non dictum sollicitudin, metus mauris malesuada diam, quis mollis odio libero in ante.</p>

      <h2 class="slide__subtitle" style="left:309px; top:88px;">Subtitle here</h2>

      <p class="copy" style="left:311px; top:111px; width:215px;">Lorem ipsum dolor sit amet, consectetur adipiscing elit. Aliquam eget bibendum dui. libero in ante lacus.</p>

      <ul class="bullet-list" style="left:318px; top:145px; width:210px;">
        <li style="padding-left:27px; height:44px;">
          <svg class="globe-icon" width="14" height="14" viewBox="0 0 14 14" aria-hidden="true"><circle cx="7" cy="7" r="6.3" fill="#2a8fd8" stroke="#8fd2f4" stroke-width="1"/><ellipse cx="7" cy="7" rx="2.6" ry="5.6" fill="none" stroke="#dff3ff" stroke-width="0.7"/><line x1="1.2" y1="7" x2="12.8" y2="7" stroke="#dff3ff" stroke-width="0.7"/><line x1="2" y1="4.3" x2="12" y2="4.3" stroke="#dff3ff" stroke-width="0.6"/><line x1="2" y1="9.7" x2="12" y2="9.7" stroke="#dff3ff" stroke-width="0.6"/></svg>
          Lorem ipsum dolor sit amet, consectetur adipiscing elit. Aliquam eget bibendum dui. libero in ante lacus.
        </li>
        <li style="padding-left:27px; height:44px;">
          <svg class="globe-icon" width="14" height="14" viewBox="0 0 14 14" aria-hidden="true"><circle cx="7" cy="7" r="6.3" fill="#2a8fd8" stroke="#8fd2f4" stroke-width="1"/><ellipse cx="7" cy="7" rx="2.6" ry="5.6" fill="none" stroke="#dff3ff" stroke-width="0.7"/><line x1="1.2" y1="7" x2="12.8" y2="7" stroke="#dff3ff" stroke-width="0.7"/><line x1="2" y1="4.3" x2="12" y2="4.3" stroke="#dff3ff" stroke-width="0.6"/><line x1="2" y1="9.7" x2="12" y2="9.7" stroke="#dff3ff" stroke-width="0.6"/></svg>
          Lorem ipsum dolor sit amet, consectetur adipiscing elit. Aliquam eget bibendum dui. libero in ante lacus.
        </li>
        <li style="padding-left:27px; height:44px;">
          <svg class="globe-icon" width="14" height="14" viewBox="0 0 14 14" aria-hidden="true"><circle cx="7" cy="7" r="6.3" fill="#2a8fd8" stroke="#8fd2f4" stroke-width="1"/><ellipse cx="7" cy="7" rx="2.6" ry="5.6" fill="none" stroke="#dff3ff" stroke-width="0.7"/><line x1="1.2" y1="7" x2="12.8" y2="7" stroke="#dff3ff" stroke-width="0.7"/><line x1="2" y1="4.3" x2="12" y2="4.3" stroke="#dff3ff" stroke-width="0.6"/><line x1="2" y1="9.7" x2="12" y2="9.7" stroke="#dff3ff" stroke-width="0.6"/></svg>
          Lorem ipsum dolor sit amet, consectetur adipiscing elit. Aliquam eget bibendum dui. libero in ante lacus.
        </li>
        <li style="padding-left:27px; height:44px;">
          <svg class="globe-icon" width="14" height="14" viewBox="0 0 14 14" aria-hidden="true"><circle cx="7" cy="7" r="6.3" fill="#2a8fd8" stroke="#8fd2f4" stroke-width="1"/><ellipse cx="7" cy="7" rx="2.6" ry="5.6" fill="none" stroke="#dff3ff" stroke-width="0.7"/><line x1="1.2" y1="7" x2="12.8" y2="7" stroke="#dff3ff" stroke-width="0.7"/><line x1="2" y1="4.3" x2="12" y2="4.3" stroke="#dff3ff" stroke-width="0.6"/><line x1="2" y1="9.7" x2="12" y2="9.7" stroke="#dff3ff" stroke-width="0.6"/></svg>
          Lorem ipsum dolor sit amet, consectetur adipiscing elit. Aliquam eget bibendum dui. libero in ante lacus.
        </li>
      </ul>

      <span class="footer-text footer-page">1</span>
      <span class="footer-text footer-title">PRESENTATION TITLE</span>
      <span class="footer-text footer-subtitle">Presentation Subtitle</span>
      <div class="footer-brand">NORTHVALE<br>HEALTH</div>
    </section>

    <!-- Single-column content slide -->
    <section class="slide slide--single-column">
      <svg class="slide__art" width="563" height="423" viewBox="0 0 563 423" aria-hidden="true">
        <defs>
          <linearGradient id="cornerCyanB" x1="0" y1="0" x2="1" y2="1">
            <stop offset="0" stop-color="#7af3f7"/>
            <stop offset="1" stop-color="#3fd0f0"/>
          </linearGradient>
          <linearGradient id="footerDarkB" x1="0" y1="0" x2="1" y2="0">
            <stop offset="0" stop-color="#1d4f9a"/>
            <stop offset="1" stop-color="#1a8fe0"/>
          </linearGradient>
          <linearGradient id="footerLightB" x1="0" y1="0" x2="1" y2="0">
            <stop offset="0" stop-color="#13a6ec"/>
            <stop offset="1" stop-color="#17c5f3"/>
          </linearGradient>
        </defs>
        <polygon points="486,0 563,0 563,102" fill="var(--corner-blue)"/>
        <polygon points="0,267 0,371 100,371" fill="url(#cornerCyanB)"/>
        <rect x="0" y="371" width="563" height="52" fill="var(--footer-blue)"/>
        <polygon points="75,371 240,371 275,423 110,423" fill="url(#footerDarkB)"/>
        <polygon points="240,371 563,371 563,423 275,423" fill="url(#footerLightB)"/>
      </svg>

      <h1 class="slide__title" style="left:43px;">TITLE HERE</h1>
      <h2 class="slide__subtitle subtitle--lead">Subtitle here</h2>

      <p class="copy" style="left:43px; top:82px; width:482px;">Lorem ipsum dolor sit amet, consectetur adipiscing elit. Fusce et diam vitae mi viverra vulputate. Suspendisse tempus in tortor vitae egestas. Nam dapibus augue non sem placerat lacinia. Pellentesque augue odio, vulputate a purus vitae, semper mollis diam. Morbi consectetur pulvinar adipiscing. Sed et consectetur urna. Mauris id tempor magna, vel feugiat arcu. Nullam fermentum elementum aliquam. Duis vitae dictum tellus.</p>

      <p class="note" style="left:43px; top:133px; width:478px; padding:8px 5px 8px;">Important notes here. Lorem ipsum dolor sit amet, consectetur adipiscing elit.</p>

      <p class="copy" style="left:43px; top:176px; width:482px;">Maecenas mattis tempor nibh non laoreet. Curabitur malesuada, urna in posuere pulvinar, massa mauris feugiat turpis, a aliquam urna magna non diam. Sed eu tempor nibh. Aenean facilisis massa libero, vitae laoreet tortor mattis quis. Praesent egestas egestas leo, porta auctor libero volutpat quis. Fusce ac iaculis enim. Sed nec dapibus augue.</p>

      <h2 class="slide__subtitle" style="left:41px; top:219px;">Subtitle here</h2>

      <p class="copy" style="left:43px; top:240px; width:482px;">Lorem ipsum dolor sit amet, consectetur adipiscing elit. Aliquam eget bibendum dui. Nunc tristique, orci non dictum sollicitudin, metus mauris malesuada diam, quis mollis odio libero in ante.</p>

      <ul class="bullet-list" style="left:43px; top:271px; width:480px;">
        <li style="padding-left:22px; height:21px; padding-top:2px;">
          <svg class="globe-icon" width="14" height="14" viewBox="0 0 14 14" aria-hidden="true"><circle cx="7" cy="7" r="6.3" fill="#2a8fd8" stroke="#8fd2f4" stroke-width="1"/><ellipse cx="7" cy="7" rx="2.6" ry="5.6" fill="none" stroke="#dff3ff" stroke-width="0.7"/><line x1="1.2" y1="7" x2="12.8" y2="7" stroke="#dff3ff" stroke-width="0.7"/><line x1="2" y1="4.3" x2="12" y2="4.3" stroke="#dff3ff" stroke-width="0.6"/><line x1="2" y1="9.7" x2="12" y2="9.7" stroke="#dff3ff" stroke-width="0.6"/></svg>
          Lorem ipsum dolor sit amet, consectetur adipiscing elit. Aliquam eget bibendum dui. libero in ante lacus.
        </li>
        <li style="padding-left:22px; height:21px; padding-top:2px;">
          <svg class="globe-icon" width="14" height="14" viewBox="0 0 14 14" aria-hidden="true"><circle cx="7" cy="7" r="6.3" fill="#2a8fd8" stroke="#8fd2f4" stroke-width="1"/><ellipse cx="7" cy="7" rx="2.6" ry="5.6" fill="none" stroke="#dff3ff" stroke-width="0.7"/><line x1="1.2" y1="7" x2="12.8" y2="7" stroke="#dff3ff" stroke-width="0.7"/><line x1="2" y1="4.3" x2="12" y2="4.3" stroke="#dff3ff" stroke-width="0.6"/><line x1="2" y1="9.7" x2="12" y2="9.7" stroke="#dff3ff" stroke-width="0.6"/></svg>
          Lorem ipsum dolor sit amet, consectetur adipiscing elit. Aliquam eget bibendum dui. libero in ante lacus.
        </li>
        <li style="padding-left:22px; height:21px; padding-top:2px;">
          <svg class="globe-icon" width="14" height="14" viewBox="0 0 14 14" aria-hidden="true"><circle cx="7" cy="7" r="6.3" fill="#2a8fd8" stroke="#8fd2f4" stroke-width="1"/><ellipse cx="7" cy="7" rx="2.6" ry="5.6" fill="none" stroke="#dff3ff" stroke-width="0.7"/><line x1="1.2" y1="7" x2="12.8" y2="7" stroke="#dff3ff" stroke-width="0.7"/><line x1="2" y1="4.3" x2="12" y2="4.3" stroke="#dff3ff" stroke-width="0.6"/><line x1="2" y1="9.7" x2="12" y2="9.7" stroke="#dff3ff" stroke-width="0.6"/></svg>
          Lorem ipsum dolor sit amet, consectetur adipiscing elit. Aliquam eget bibendum dui. libero in ante lacus.
        </li>
      </ul>

      <span class="footer-text footer-page">1</span>
      <span class="footer-text footer-title">PRESENTATION TITLE</span>
      <span class="footer-text footer-subtitle">Presentation Subtitle</span>
      <div class="footer-brand">NORTHVALE<br>HEALTH</div>
    </section>

  </div>
</body>
</html>
```